Quality Monitoring Company Needs a New Site

We are an established company that has a fair number of clients but the site lacks current design standards that we'd like to keep up with. We'd like to mimic the same style of the site on plinkora.com, vetrumo.com, https://brindlecoffer.com/, etc. We'd also like to make sure the designer understands SEO Silos and how it effects the design elements. Attached is the structure that I'd like to follow for the pages. You don't need to design every single sub-page because they'll probably be fairly similar; however, I want to see at least 1 each. Please use the content on our current site for filler areas. Please try to do a good job of understanding what we do so you can use your best judgement on what is needed to be successful. Use our color scheme and the logo should be the side view but I included the AI just in case.
Updates

I am narrowing down on the field of designs that I have received. There are a lot of similarities between the designs I like and don't like. I'd also like to ensure that some of the inner pages get done in the next 5 days so I can see the creativity that is there as well. That is probably what is next -- getting a few inner pages completed so I can see what you can come up with (not based on our current website) because the current "front pages" are all so good and so close.

Industry/Entity Type

Telecommunications

Colors

Designer to choose colors to be used in the design.

Requirements
Must have
• SEO Silo Look and Feel
• Current Colors
Should not have
• No stockphotos whatsoever. NONE.

```html
<!DOCTYPE html>
<html lang="en">
<head>
<meta charset="utf-8">
<title>Dialvera — Call Quality Monitoring</title>
<link href="https://fonts.googleapis.com/css2?family=Montserrat:wght@300;400;500;600;700&family=Raleway:wght@400;500;600;700&display=swap" rel="stylesheet">
<style>
:root{
  --navy:#0b2a4c;
  --navy-deep:#081d38;
  --blue:#1a7fd8;
  --sky:#23a6e6;
  --pale:#e2f2fb;
  --pale-2:#cde9f8;
  --text:#333d4a;
  --muted:#6b7785;
  --line:#e6ebf0;
  --white:#ffffff;
}
*{box-sizing:border-box;margin:0;padding:0}
html,body{width:1200px;height:4938px;overflow:hidden;background:var(--white)}
body{position:relative;font-family:"Raleway",sans-serif;color:var(--text)}
.abs{position:absolute}
a{color:inherit;text-decoration:none}

/* header */
.brand{position:absolute;font-family:"Montserrat",sans-serif;font-weight:600;color:var(--navy);letter-spacing:-1px}
.site-nav{position:absolute;left:389px;top:36px;display:flex;gap:32px;font-family:"Raleway",sans-serif;font-size:16px;color:var(--navy);font-weight:500}
.site-nav .active{color:var(--white)}
.btn-login{position:absolute;left:1010px;top:30px;width:100px;height:42px;border-radius:21px;background:var(--navy);color:#fff;font-family:"Montserrat",sans-serif;font-size:15px;font-weight:600;display:flex;align-items:center;justify-content:center}

.hero-title{position:absolute;left:663px;top:160px;font-family:"Montserrat",sans-serif;font-size:86px;font-weight:600;color:var(--navy);letter-spacing:-1px;line-height:1}
.hero-sub{position:absolute;left:666px;top:278px;width:450px;font-size:22px;line-height:32px;color:var(--muted)}
.btn{position:absolute;display:flex;align-items:center;justify-content:center;gap:8px;border:2px solid var(--navy);border-radius:40px;color:var(--navy);font-family:"Montserrat",sans-serif;font-weight:600}
.btn.sm{border-color:var(--blue);color:var(--blue);font-size:15px}
.btn .dot{width:14px;height:14px;border-radius:50%;background:currentColor;display:inline-flex;align-items:center;justify-content:center}
.btn .dot::after{content:"";border-left:5px solid #fff;border-top:3.5px solid transparent;border-bottom:3.5px solid transparent;margin-left:2px}

.section-title{position:absolute;font-family:"Montserrat",sans-serif;font-size:38px;font-weight:500;color:#111;line-height:1}
.section-title .light{color:var(--sky);font-weight:300}
.centered{left:0;width:1200px;text-align:center}
.phone-mark{position:absolute}
.para{position:absolute;font-size:15px;line-height:32px;color:var(--text)}

/* service tiles */
.tile{position:absolute;width:207px;height:207px;border-radius:6px;color:#fff;display:flex;flex-direction:column;align-items:center;justify-content:flex-end;padding-bottom:30px;text-align:center;font-size:20px;line-height:27px;font-family:"Raleway",sans-serif;box-shadow:0 10px 24px rgba(8,29,56,.18)}
.tile svg{margin-bottom:18px}
.tile.bright{background:linear-gradient(160deg,#1fb0ee,#1681d6)}
.tile.dark{background:linear-gradient(160deg,#0e3a66,#081d38)}

/* pricing */
.plan{position:absolute;top:2456px;width:238px;height:341px;border-radius:4px;color:#fff;text-align:center;font-family:"Raleway",sans-serif}
.plan.bright{background:linear-gradient(170deg,#1ea7ea,#1565c4)}
.plan.dark{background:linear-gradient(170deg,#0d3560,#081d38)}
.plan h3{margin-top:30px;font-family:"Montserrat",sans-serif;font-size:26px;font-weight:600}
.price{margin:16px auto 0;width:94px;height:94px;border-radius:50%;display:flex;align-items:center;justify-content:center;font-family:"Montserrat",sans-serif;font-size:40px;font-weight:500}
.plan.bright .price{background:var(--navy-deep)}
.plan.dark .price{background:var(--blue)}
.price small{font-size:14px;margin-top:14px}
.plan ul{list-style:none;margin-top:16px;font-size:18px;line-height:31px;color:rgba(255,255,255,.85)}
.plan .sign{margin:20px auto 0;width:122px;height:40px;border-radius:20px;background:#fff;color:var(--navy);font-family:"Montserrat",sans-serif;font-weight:700;font-size:15px;display:flex;align-items:center;justify-content:center}

/* team */
.member{position:absolute;top:3110px;width:240px;text-align:center}
.avatar{margin:0 auto;width:104px;height:104px;border-radius:50%;background:linear-gradient(160deg,#d9dde2,#9aa3ad)}
.member h4{margin-top:24px;font-family:"Montserrat",sans-serif;font-size:17px;font-weight:500;color:#111}
.member p{margin-top:10px;font-size:13px;color:var(--text)}
.divider-v{position:absolute;top:3086px;width:1px;height:232px;background:var(--line)}

/* blog */
.post{position:absolute;top:3521px;width:286px;height:361px;background:#fff;box-shadow:0 4px 18px rgba(0,0,0,.12);padding:6px}
.post .thumb{height:167px;position:relative}
.post .date{position:absolute;left:20px;bottom:-2px;background:var(--blue);color:#fff;font-size:13px;font-weight:600;padding:6px 12px}
.post h4{margin:30px 18px 0;font-family:"Montserrat",sans-serif;font-size:17px;font-weight:600;color:#111}
.post p{margin:20px 18px 0;font-size:14px;line-height:26px;color:var(--muted)}
.post a{display:block;margin:10px 18px 0;color:var(--blue);font-weight:700;font-size:15px;text-decoration:underline}

/* contact */
.contact-item{position:absolute;left:90px;display:flex;align-items:center;gap:20px;color:#fff;font-size:15px;line-height:22px}
.contact-item .ic{width:44px;height:44px;border:1.5px solid rgba(255,255,255,.8);border-radius:50%;display:flex;align-items:center;justify-content:center;flex:none}
.field{position:absolute;border:1px solid #cfd6dd;border-radius:26px;padding:0 20px;font-size:15px;color:#8a949e;display:flex;align-items:center;height:50px}
.field.area{align-items:flex-start;padding-top:16px;height:88px}

/* footer */
.foot-rule{position:absolute;left:90px;top:4624px;width:1020px;height:1px;background:var(--line)}
.foot-nav{position:absolute;left:0;top:4767px;width:1200px;text-align:center;font-size:15px;color:var(--muted)}
.foot-nav span.sep{margin:0 14px}
.social{position:absolute;top:4817px;left:503px;display:flex;gap:8px}
.social i{width:42px;height:42px;border:2px solid var(--navy);border-radius:50%;display:block}
.copy{position:absolute;left:0;width:1200px;top:4888px;text-align:center;font-size:12px;color:var(--muted)}
</style>
</head>
<body>

<!-- HERO -->
<svg class="abs" style="left:0;top:0" width="600" height="560" viewBox="0 0 600 560" aria-hidden="true">
  <defs><linearGradient id="heroBlue" x1="0" y1="0" x2="1" y2="1"><stop offset="0" stop-color="#1fa6ea"/><stop offset="1" stop-color="#1270d0"/></linearGradient></defs>
  <path d="M340 0 H570 C575 150 560 330 470 440 C380 545 200 570 60 540 C20 532 0 520 0 500 V0 Z" fill="url(#heroBlue)"/>
</svg>
<div class="abs" role="img" aria-label="Illustration of a call agent on the phone at a laptop, with plants and coffee cup" style="left:30px;top:140px;width:540px;height:330px;border-radius:140px 160px 40px 60px;background:linear-gradient(160deg,#e4f3fc,#bfe3f7)"></div>

<div class="brand" style="left:90px;top:24px;font-size:48px">Dialvera</div>
<nav class="site-nav">
  <a class="active">Home</a><a>Industries</a><a>Services</a><a>Pricing</a><a>Team</a><a>Blog</a><a>Contact Us</a>
</nav>
<a class="btn-login">LOGIN</a>

<h1 class="hero-title">Dialvera</h1>
<p class="hero-sub">Lorem ipsum dolor sit amet, consectetur adipiscing elit, sed do eiusmod</p>
<a class="btn" style="left:667px;top:387px;width:270px;height:68px;font-size:21px">GET STARTED <span class="dot"></span></a>
<svg class="abs" style="left:580px;top:512px" width="42" height="42" viewBox="0 0 42 42" aria-hidden="true"><rect x="1" y="1" width="40" height="40" rx="8" fill="none" stroke="#0b2a4c" stroke-width="2"/><path d="M16 19 L21 24 L26 19" fill="none" stroke="#0b2a4c" stroke-width="2"/></svg>

<!-- WELCOME -->
<h2 class="section-title centered" style="top:702px">Welcome to <b style="font-weight:600">Dialvera</b></h2>
<svg class="phone-mark" style="left:580px;top:762px" width="40" height="40" viewBox="0 0 24 24" aria-hidden="true"><path d="M6.6 10.8a15 15 0 006.6 6.6l2.2-2.2c.3-.3.7-.4 1-.2 1.1.4 2.3.6 3.6.6.6 0 1 .4 1 1V20c0 .6-.4 1-1 1A17 17 0 013 4c0-.6.4-1 1-1h3.5c.6 0 1 .4 1 1 0 1.3.2 2.5.6 3.6.1.3 0 .7-.2 1z" fill="#cfe9f8"/></svg>
<p class="para" style="left:122px;top:816px;width:956px;text-align:center">Lorem ipsum dolor sit amet, consectetur adipiscing elit, sed do eiusmod tempor incididunt ut labore et dolore magna aliqua. Ut enim ad minim veniam, quis nostrud exercitation ullamco laboris nisi ut aliquip ex ea commodo consequat. Duis aute irure dolor in reprehenderit in voluptate velit esse cillum dolore eu fugiat nulla pariatur.</p>
<a class="btn sm" style="left:510px;top:949px;width:180px;height:54px;border-color:var(--navy);color:var(--blue)">READ MORE <span class="dot"></span></a>

<!-- SERVICES -->
<svg class="abs" style="left:630px;top:1100px" width="570" height="540" viewBox="0 0 570 540" aria-hidden="true">
  <defs><linearGradient id="svcBlue" x1="0" y1="0" x2="1" y2="1"><stop offset="0" stop-color="#1da4ea"/><stop offset="1" stop-color="#1262c9"/></linearGradient></defs>
  <path d="M570 0 V536 C470 520 360 500 250 470 C120 440 -10 380 4 290 C20 190 150 150 260 110 C380 70 470 20 570 0 Z" fill="url(#svcBlue)"/>
</svg>
<h2 class="section-title" style="left:90px;top:1183px">Our <span class="light">Services</span></h2>
<svg class="phone-mark" style="left:90px;top:1240px" width="40" height="40" viewBox="0 0 24 24" aria-hidden="true"><path d="M6.6 10.8a15 15 0 006.6 6.6l2.2-2.2c.3-.3.7-.4 1-.2 1.1.4 2.3.6 3.6.6.6 0 1 .4 1 1V20c0 .6-.4 1-1 1A17 17 0 013 4c0-.6.4-1 1-1h3.5c.6 0 1 .4 1 1 0 1.3.2 2.5.6 3.6.1.3 0 .7-.2 1z" fill="#cfe9f8"/></svg>
<p class="para" style="left:90px;top:1298px;width:462px;text-align:justify">Lorem ipsum dolor sit amet, consectetur adipiscing elit, sed do eiusmod tempor incididunt ut labore et dolore magna aliqua. Ut enim ad minim veniam, quis nostrud exercitation ullamco laboris nisi ut aliquip ex ea commodo consequat. Duis aute irure dolor in reprehenderit in voluptate velit esse cillum dolore eu fugiat nulla pariatur.</p>
<a class="btn sm" style="left:92px;top:1520px;width:182px;height:52px;border-color:var(--navy);color:var(--blue)">READ MORE <span class="dot"></span></a>

<div class="tile bright" style="left:654px;top:1146px">
  <svg width="70" height="62" viewBox="0 0 70 62" fill="none" stroke="#fff" stroke-width="2"><circle cx="24" cy="24" r="14"/><circle cx="24" cy="24" r="6"/><path d="M40 22 L58 28 V42 C58 52 48 58 48 58 C48 58 38 52 38 42 V28 Z"/><path d="M43 41 L47 45 L54 36"/></svg>
  Quality<br>Assurance</div>
<div class="tile dark" style="left:882px;top:1188px">
  <svg width="70" height="62" viewBox="0 0 70 62" fill="none" stroke="#fff" stroke-width="2"><rect x="12" y="6" width="46" height="36" rx="2"/><path d="M4 48 H66 V54 H4 Z"/><circle cx="35" cy="20" r="5"/><path d="M25 36 C25 29 45 29 45 36"/></svg>
  Coaching</div>
<div class="tile dark" style="left:654px;top:1374px">
  <svg width="70" height="62" viewBox="0 0 70 62" fill="none" stroke="#fff" stroke-width="2"><circle cx="42" cy="20" r="16"/><path d="M35 28 L49 12"/><circle cx="36" cy="14" r="2.5"/><circle cx="48" cy="26" r="2.5"/><path d="M4 46 H18 C24 46 28 50 34 50 H48 L60 42 C64 40 66 44 62 48 L50 58 H4"/></svg>
  Sales<br>Performance</div>
<div class="tile dark" style="left:882px;top:1416px">
  <svg width="70" height="62" viewBox="0 0 70 62" fill="none" stroke="#fff" stroke-width="2"><path d="M2 10 L8 4 L14 14 L20 4 L26 14 L32 4 L38 14 L44 4 L50 14 L56 4 L62 14 L68 6"/><rect x="26" y="20" width="18" height="28" rx="9"/><path d="M30 28 H40 M30 34 H40 M30 40 H40 M35 48 V58 M27 58 H43"/></svg>
  AI Enabled<br>Voice Analytics</div>

<!-- INDUSTRIES -->
<div class="abs" role="img" aria-label="Illustration of a smartphone showing the brand, a jumping woman and bubbles labelled Education, Insurance, Home Services, Utilities, Financial Services, Call Tracking, Mortgage and Automotive" style="left:38px;top:1740px;width:590px;height:450px;border-radius:200px 230px 180px 160px;background:linear-gradient(160deg,#e6f4fc,#c8e6f8)"></div>
<h2 class="section-title" style="left:696px;top:1804px">Our <span class="light">Industries</span></h2>
<svg class="phone-mark" style="left:696px;top:1860px" width="40" height="40" viewBox="0 0 24 24" aria-hidden="true"><path d="M6.6 10.8a15 15 0 006.6 6.6l2.2-2.2c.3-.3.7-.4 1-.2 1.1.4 2.3.6 3.6.6.6 0 1 .4 1 1V20c0 .6-.4 1-1 1A17 17 0 013 4c0-.6.4-1 1-1h3.5c.6 0 1 .4 1 1 0 1.3.2 2.5.6 3.6.1.3 0 .7-.2 1z" fill="#cfe9f8"/></svg>
<p class="para" style="left:696px;top:1921px;width:412px;text-align:justify">Lorem ipsum dolor sit amet, consectetur adipiscing elit, sed do eiusmod tempor incididunt ut labore et dolore magna aliqua. Ut enim ad minim veniam, quis nostrud exercitation ullamco laboris nisi ut aliquip ex ea commodo consequat.</p>
<a class="btn sm" style="left:700px;top:2110px;width:180px;height:52px">READ MORE <span class="dot"></span></a>

<!-- PRICING -->
<svg class="abs" style="left:150px;top:2300px" width="900" height="590" viewBox="0 0 900 590" aria-hidden="true">
  <path d="M230 90 C300 0 460 -10 560 50 C640 100 760 110 800 180 C850 270 790 380 720 450 C620 550 460 540 330 520 C200 500 90 470 80 380 C70 280 170 170 230 90 Z" fill="#e2f2fb"/>
  <circle cx="76" cy="100" r="13" fill="#e2f2fb"/><circle cx="726" cy="92" r="13" fill="#e2f2fb"/><circle cx="415" cy="556" r="24" fill="#e2f2fb"/><circle cx="750" cy="540" r="24" fill="#e2f2fb"/>
</svg>
<div class="abs" role="img" aria-label="Illustration of a blue leafy plant" style="left:40px;top:2670px;width:150px;height:140px;border-radius:60% 40% 40% 60%;background:linear-gradient(160deg,#4cc0f1,#1478d4);opacity:.85"></div>
<h2 class="section-title centered" style="top:2325px">Pricing</h2>
<svg class="phone-mark" style="left:580px;top:2380px" width="40" height="40" viewBox="0 0 24 24" aria-hidden="true"><path d="M6.6 10.8a15 15 0 006.6 6.6l2.2-2.2c.3-.3.7-.4 1-.2 1.1.4 2.3.6 3.6.6.6 0 1 .4 1 1V20c0 .6-.4 1-1 1A17 17 0 013 4c0-.6.4-1 1-1h3.5c.6 0 1 .4 1 1 0 1.3.2 2.5.6 3.6.1.3 0 .7-.2 1z" fill="#ffffff"/></svg>

<div class="plan bright" style="left:217px"><h3>Basic</h3><div class="price"><small>$</small>99</div><ul><li>Lorem ipsum</li><li>Lorem ipsum dolor</li><li>Lorem ipsum</li></ul><a class="sign">SIGN IN</a></div>
<div class="plan dark" style="left:481px"><h3>Standard</h3><div class="price"><small>$</small>129</div><ul><li>Lorem ipsum</li><li>Lorem ipsum dolor</li><li>Lorem ipsum</li></ul><a class="sign">SIGN IN</a></div>
<div class="plan bright" style="left:746px"><h3>Premium</h3><div class="price"><small>$</small>222</div><ul><li>Lorem ipsum</li><li>Lorem ipsum dolor</li><li>Lorem ipsum</li></ul><a class="sign">SIGN IN</a></div>

<!-- TEAM -->
<h2 class="section-title centered" style="top:2958px">Our <span class="light">Team</span></h2>
<svg class="phone-mark" style="left:580px;top:3012px" width="40" height="40" viewBox="0 0 24 24" aria-hidden="true"><path d="M6.6 10.8a15 15 0 006.6 6.6l2.2-2.2c.3-.3.7-.4 1-.2 1.1.4 2.3.6 3.6.6.6 0 1 .4 1 1V20c0 .6-.4 1-1 1A17 17 0 013 4c0-.6.4-1 1-1h3.5c.6 0 1 .4 1 1 0 1.3.2 2.5.6 3.6.1.3 0 .7-.2 1z" fill="#cfe9f8"/></svg>
<div class="member" style="left:123px"><div class="avatar" role="img" aria-label="Team member portrait"></div><h4>SED UT PERSPICIATIS</h4><p>Lorem ipsuma</p></div>
<div class="divider-v" style="left:381px"></div>
<div class="member" style="left:373px"><div class="avatar" role="img" aria-label="Team member portrait"></div><h4>LOREM IPSUM</h4><p>Lorem ipsuma</p></div>
<div class="divider-v" style="left:600px"></div>
<div class="member" style="left:620px"><div class="avatar" role="img" aria-label="Team member portrait"></div><h4>SED UT PERSPICIATIS</h4><p>Lorem ipsuma</p></div>
<div class="divider-v" style="left:872px"></div>
<div class="member" style="left:867px"><div class="avatar" role="img" aria-label="Team member portrait"></div><h4>LOREM IPSUM</h4><p>Lorem ipsuma</p></div>

<!-- BLOG -->
<h2 class="section-title centered" style="top:3400px">Our <span class="light">Blog</span></h2>
<svg class="phone-mark" style="left:580px;top:3456px" width="40" height="40" viewBox="0 0 24 24" aria-hidden="true"><path d="M6.6 10.8a15 15 0 006.6 6.6l2.2-2.2c.3-.3.7-.4 1-.2 1.1.4 2.3.6 3.6.6.6 0 1 .4 1 1V20c0 .6-.4 1-1 1A17 17 0 013 4c0-.6.4-1 1-1h3.5c.6 0 1 .4 1 1 0 1.3.2 2.5.6 3.6.1.3 0 .7-.2 1z" fill="#cfe9f8"/></svg>
<article class="post" style="left:140px"><div class="thumb" role="img" aria-label="Blog image of a man working at a desk" style="background:linear-gradient(160deg,#6f7a84,#2c333a)"><span class="date">Aug 17 2018</span></div><h4>SED UT PERSPICIATIS UND</h4><p>Sed ut perspiciatis unde omnis iste natus error sit voluptatem tium</p><a>Read more</a></article>
<article class="post" style="left:452px"><div class="thumb" role="img" aria-label="Blog image of a process diagram on a whiteboard" style="background:linear-gradient(160deg,#f2f5f8,#b9c7d6)"><span class="date">Aug 17 2018</span></div><h4>SED UT PERSPICIATIS UND</h4><p>Sed ut perspiciatis unde omnis iste natus error sit voluptatem tium</p><a>Read more</a></article>
<article class="post" style="left:765px"><div class="thumb" role="img" aria-label="Blog image of a dart hitting a data target" style="background:linear-gradient(160deg,#b01e1e,#3a0c0c)"><span class="date">Aug 17 2018</span></div><h4>SED UT PERSPICIATIS UND</h4><p>Sed ut perspiciatis unde omnis iste natus error sit voluptatem tium</p><a>Read more</a></article>

<!-- CONTACT -->
<svg class="abs" style="left:0;top:3938px" width="480" height="600" viewBox="0 0 480 600" aria-hidden="true">
  <defs><linearGradient id="ctBlue" x1="0" y1="0" x2="1" y2="1"><stop offset="0" stop-color="#1fa6ea"/><stop offset="1" stop-color="#1160c8"/></linearGradient></defs>
  <path d="M0 0 C150 20 330 100 420 220 C500 330 440 440 320 500 C220 550 90 580 0 595 Z" fill="url(#ctBlue)"/>
</svg>
<h2 class="section-title" style="left:90px;top:4115px;color:#fff">Contact <span style="font-weight:300">Us</span></h2>
<div class="contact-item" style="top:4195px"><span class="ic"><svg width="18" height="18" viewBox="0 0 24 24"><path d="M12 2a7 7 0 00-7 7c0 5 7 13 7 13s7-8 7-13a7 7 0 00-7-7zm0 9.5A2.5 2.5 0 1112 6a2.5 2.5 0 010 5.5z" fill="#fff"/></svg></span><span>4410 Harbor Crest Ave.<br>Seabrook, CA 90412</span></div>
<div class="contact-item" style="top:4260px"><span class="ic"><svg width="18" height="18" viewBox="0 0 24 24"><path d="M6.6 10.8a15 15 0 006.6 6.6l2.2-2.2c.3-.3.7-.4 1-.2 1.1.4 2.3.6 3.6.6.6 0 1 .4 1 1V20c0 .6-.4 1-1 1A17 17 0 013 4c0-.6.4-1 1-1h3.5c.6 0 1 .4 1 1 0 1.3.2 2.5.6 3.6.1.3 0 .7-.2 1z" fill="#fff"/></svg></span><span>800-555-0173</span></div>
<div class="contact-item" style="top:4324px"><span class="ic"><svg width="18" height="18" viewBox="0 0 24 24"><path d="M3 5h18v14H3z" fill="#fff"/><path d="M3 5l9 8 9-8" fill="none" stroke="#1a7fd8" stroke-width="1.6"/></svg></span><span>Hello(at)Dialvera.com</span></div>

<h2 class="section-title" style="left:540px;top:4115px">Get In <span class="light">Touch</span></h2>
<div class="field" style="left:540px;top:4194px;width:277px">Name</div>
<div class="field" style="left:834px;top:4194px;width:274px">Phone No</div>
<div class="field" style="left:540px;top:4261px;width:277px">Email Address</div>
<div class="field" style="left:834px;top:4261px;width:274px">Subject</div>
<div class="field area" style="left:540px;top:4330px;width:568px">Message</div>
<a class="btn sm" style="left:542px;top:4437px;width:181px;height:52px;border-color:var(--navy);color:var(--blue)">SUBMIT <span class="dot"></span></a>

<!-- FOOTER -->
<div class="foot-rule"></div>
<div class="brand" style="left:0;width:1200px;text-align:center;top:4684px;font-size:60px">Dialvera</div>
<nav class="foot-nav">Home<span class="sep">|</span>Industries<span class="sep">|</span>Services<span class="sep">|</span>Pricing<span class="sep">|</span>Team<span class="sep">|</span>Blog<span class="sep">|</span>Contact Us</nav>
<div class="social" aria-label="Social links"><i></i><i></i><i></i><i></i></div>
<p class="copy">© 2019 The Company Name All rights reserved</p>

</body>
</html>
```